Harborview Estates Business Card for Apartment Buildings

Create business cards for resident managers who run apartment buildings. The audience is the public who are searching for apartment rentals, and current residents who live at the apartment building. Key design element will be incorporating the company logo, however, the logo cannot dominate. The building name and manager name are more important than the logo. Current business card design leaves little room for copy, so we may need to reduce the size on the current card to allow for more space for copy.

Target Market(s)

Adults 18-65 years of age, who are looking for an apartment rental, plus current residents who live at our apartment buildings.

Industry/Entity Type

Property Management

Contact Information for Business Card

A major design element will be use of the company logo. Important property and manager contact information must be part of the design. The size of the logo will need to be reduced to make room for building and manager contact copy.

Font styles to use
Sans Serif

Colors
3176b5
000000
959595
ffffff

Requirements
Must have
• 1) Incorporate the company logo.
• 2) Use the company colors (dark blue, black/grey, over white).
• 3) FEATURE THE BUILDING NAME
• 4) FEATURE THE MANAGER NAME
• 5) The company name is less important than BUILDING and MANAGER
• 6) Manager contact information
• **SEE ATTACHED CREATIVE BRIEF**
Nice to have
• 1) Back of card logo watermark
• 2) Ability to write notes on back of carfd
Should not have
• Avoid letting the company logo dominate the card, the building name and manager are more important than the company logo.

```html
<!DOCTYPE html>
<html lang="en">
<head>
<meta charset="utf-8">
<title>Harborview Estates – Business Card</title>
<link href="https://fonts.googleapis.com/css2?family=Roboto:wght@400;700&display=swap" rel="stylesheet">
<style>
  :root {
    --brand-blue: #3176b5;
    --charcoal: #444548;
    --mid-grey: #959595;
    --white: #ffffff;
    --stage: #e9e9ea;
  }
  * { box-sizing: border-box; margin: 0; padding: 0; }
  html, body {
    width: 1200px; height: 930px; overflow: hidden;
    background: var(--stage);
    font-family: "Roboto", Arial, sans-serif;
  }
  .card {
    position: absolute;
    width: 540px; height: 309px;
    border-radius: 14px;
    overflow: hidden;
    box-shadow: 0 6px 18px rgba(0,0,0,0.18);
  }
  /* Back side */
  .card-back {
    left: 40px; top: 230px;
    background: var(--charcoal);
    color: var(--white);
  }
  .card-back .brand {
    position: absolute; left: 0; right: 0; top: 112px;
    display: flex; align-items: center; justify-content: center; gap: 12px;
  }
  .brand-dot {
    width: 18px; height: 18px; border-radius: 50%;
    background: currentColor; flex: none;
  }
  .brand-name {
    font-weight: 700; font-size: 30px; letter-spacing: 0.5px;
    text-transform: uppercase; line-height: 1;
  }
  .card-back .website {
    position: absolute; left: 0; right: 0; bottom: 44px;
    text-align: center; font-size: 14px; letter-spacing: 0.5px;
  }
  /* Front side */
  .card-front {
    left: 620px; top: 370px;
    background: var(--white);
  }
  .card-front .wave { position: absolute; inset: 0; }
  .card-front .brand {
    position: absolute; left: 36px; top: 140px;
    display: flex; align-items: center; gap: 10px;
    color: var(--brand-blue);
  }
  .card-front .brand-name {
    font-size: 22px; line-height: 1.15; width: 150px;
  }
  .manager {
    position: absolute; right: 34px; top: 12px; text-align: right;
  }
  .manager-name {
    color: var(--brand-blue); font-weight: 700; font-size: 20px; line-height: 1.2;
  }
  .manager-title {
    color: var(--charcoal); font-size: 12px; line-height: 1.3; margin-top: 1px;
  }
  .contact {
    position: absolute; right: 26px; top: 142px;
    color: var(--white); text-align: right;
    font-size: 12px; line-height: 1.45;
  }
  .contact .address { margin-bottom: 8px; }
  .contact-line {
    display: flex; align-items: center; justify-content: flex-end; gap: 7px;
  }
  .contact-line svg { width: 10px; height: 10px; flex: none; }
</style>
</head>
<body>

<section class="card card-back" aria-label="Card back">
  <div class="brand">
    <span class="brand-dot"></span>
    <span class="brand-name">Harborview Estates LLC</span>
  </div>
  <p class="website">www.harborviewest.com</p>
</section>

<section class="card card-front" aria-label="Card front">
  <svg class="wave" viewBox="0 0 540 309" preserveAspectRatio="none" aria-hidden="true">
    <path d="M540,70 C400,58 360,120 320,195 C285,262 200,280 0,262 L0,309 L540,309 Z" fill="var(--charcoal)"/>
    <path d="M0,248 C150,250 230,240 280,212" fill="none" stroke="var(--mid-grey)" stroke-width="10" opacity="0.5"/>
    <path d="M540,62 C396,50 354,114 312,191 C278,258 200,274 0,255" fill="none" stroke="var(--brand-blue)" stroke-width="5"/>
    <path d="M540,66 C398,54 357,117 316,193" fill="none" stroke="var(--white)" stroke-width="2"/>
  </svg>

  <div class="brand">
    <span class="brand-dot"></span>
    <span class="brand-name">Harborview Estates LLC</span>
  </div>

  <div class="manager">
    <p class="manager-name">Marisol Delgado</p>
    <p class="manager-title">Resident Manager</p>
  </div>

  <div class="contact">
    <div class="address">
      <p>Bayside Court Apartments</p>
      <p>2841 Linden Avenue</p>
      <p>Seaport, CA 92990</p>
    </div>
    <p class="contact-line">555-210-4471
      <svg viewBox="0 0 10 10"><path d="M2 1 L4 1 L4.6 3 L3.4 3.8 Q4.4 5.8 6.2 6.6 L7 5.4 L9 6 L9 8 Q5 9 1.5 4.5 Q1 3 2 1Z" fill="currentColor"/></svg>
    </p>
    <p class="contact-line">555-318-2290
      <svg viewBox="0 0 10 10"><rect x="2.5" y="0.5" width="5" height="9" rx="1" fill="none" stroke="currentColor"/><circle cx="5" cy="8" r="0.6" fill="currentColor"/></svg>
    </p>
    <p class="contact-line">555-604-1185
      <svg viewBox="0 0 10 10"><rect x="1" y="3" width="8" height="5" rx="1" fill="currentColor"/><rect x="3" y="1" width="4" height="2" fill="currentColor"/></svg>
    </p>
    <p class="contact-line">marisol@harborviewest.com
      <svg viewBox="0 0 10 10"><rect x="0.5" y="2" width="9" height="6" fill="none" stroke="currentColor"/><path d="M0.5 2 L5 5.5 L9.5 2" fill="none" stroke="currentColor"/></svg>
    </p>
    <p class="contact-line">www.harborviewest.com
      <svg viewBox="0 0 10 10"><circle cx="5" cy="5" r="4.3" fill="none" stroke="currentColor"/><path d="M0.7 5 H9.3 M5 0.7 Q2.5 5 5 9.3 M5 0.7 Q7.5 5 5 9.3" fill="none" stroke="currentColor" stroke-width="0.8"/></svg>
    </p>
  </div>
</section>

</body>
</html>
```